Master Label Design for Velmora Botanic Products

Looking to update product labels and add consistency across our line with a new master label design. 'Velmora Botanic' has been a trusted name in the health marketplace providing quality herbal and dietary supplements since 1979. We have 8 products in need of a master label design, examples of our current labels are attached, and you can see more at our website, VelmoraBotanic.com. All 8 products currently have a 160mm x 58mm label size, while 3 products also have a 194mm x 68mm (Chaparral, Garlic Bright, and Bulvana Odorless Garlic).
Also, our logo is only prominent on the EDTA label, but that product is our #1 seller and most recognizable, it is at the artist's discretion what to do with our logo. (attached, if needed).
Please show me only the label designs for "EDTA".
Target Market(s)
-Health-conscious adults over 40 in North America who buy herbal and/or dietary supplements.
-->Cardiovascular health-conscious adults (a.k.a., "heart healthy" adults)
-->Adults with poor cardiovascular health seeking naturopathic/alternative options.
Industry/Entity Type
Health And Wellness
Logo Text
Velmora Botanic
Colors
Designer to choose colors to be used in the design.

```html
<!DOCTYPE html>
<html lang="en">
<head>
<meta charset="utf-8">
<title>Velmora Botanic – EDTA Label</title>
<link rel="stylesheet" href="https://fonts.googleapis.com/css2?family=Raleway:wght@300;500;700&display=swap">
<style>
  :root {
    --backdrop: #9b9b9b;
    --label-green: #64c964;
    --brush-green: #2fae4f;
    --brand-teal: #1d8a78;
    --gold-light: #f3d27a;
    --gold-dark: #b8862b;
    --accent-yellow: #f2e35a;
    --wordmark: #8c2b4c;
    --ink-dark: #2b4a2b;
    --white: #ffffff;
  }
  html, body {
    margin: 0;
    padding: 0;
    width: 1200px;
    height: 825px;
    overflow: hidden;
    background: var(--backdrop);
  }
  .label-canvas {
    display: block;
    width: 1200px;
    height: 825px;
    font-family: "Raleway", sans-serif;
  }
  .label-body { fill: var(--label-green); }
  .brand-line {
    fill: var(--brand-teal);
    font-weight: 700;
    font-size: 15px;
    letter-spacing: 7px;
  }
  .brush-area { fill: var(--brush-green); }
  .hex-frame { fill: none; stroke: url(#goldStroke); stroke-width: 5; }
  .wordmark {
    fill: var(--wordmark);
    font-weight: 700;
    font-size: 26px;
  }
  .product-name {
    fill: var(--white);
    font-weight: 300;
    font-size: 96px;
    letter-spacing: 6px;
  }
  .latin-name {
    fill: var(--accent-yellow);
    font-weight: 500;
    font-size: 13px;
    letter-spacing: 1px;
  }
  .gold-rule { stroke: var(--accent-yellow); stroke-width: 2.5; }
  .ingredients {
    fill: var(--accent-yellow);
    font-weight: 700;
    font-size: 17px;
    letter-spacing: 0.5px;
  }
  .count {
    fill: var(--ink-dark);
    font-weight: 700;
    font-size: 38px;
  }
  .count-unit {
    fill: var(--ink-dark);
    font-weight: 700;
    font-size: 13px;
    letter-spacing: 1px;
  }
</style>
</head>
<body>
<svg class="label-canvas" viewBox="0 0 1200 825" xmlns="http://www.w3.org/2000/svg">
  <defs>
    <linearGradient id="goldStroke" x1="0" y1="0" x2="1" y2="1">
      <stop offset="0" stop-color="#f3d27a"/>
      <stop offset="0.5" stop-color="#b8862b"/>
      <stop offset="1" stop-color="#f3d27a"/>
    </linearGradient>
  </defs>

  <rect class="label-body" x="150" y="130" width="900" height="570"/>

  <text class="brand-line" x="600" y="200" text-anchor="middle">VELMORA BOTANIC</text>

  <path class="brush-area" role="img" aria-label="Painted green brush stroke texture"
        d="M300 360 C360 320 470 315 560 325 C680 300 800 330 880 360 C910 400 905 470 870 520 C790 560 660 565 560 555 C450 570 350 555 310 520 C280 470 285 400 300 360 Z"/>

  <polygon class="hex-frame" points="600,225 835,340 835,565 600,680 365,565 365,340"/>

  <text class="wordmark" x="600" y="330" text-anchor="middle">Velmora Botanic</text>

  <text class="product-name" x="600" y="435" text-anchor="middle">EDTA</text>
  <text class="latin-name" x="600" y="460" text-anchor="middle">(ETHYLENEDIAMINE TETRAACETIC ACID)</text>

  <line class="gold-rule" x1="478" y1="482" x2="760" y2="482"/>

  <text class="ingredients" x="488" y="512">WITH GARLIC, VIT. C,</text>
  <text class="ingredients" x="488" y="536">ZINC AND CAYENNE</text>

  <text class="count" x="600" y="610" text-anchor="middle">90</text>
  <text class="count-unit" x="600" y="630" text-anchor="middle">CAPSULES</text>
</svg>
</body>
</html>
```